KRV Business Card

Looking for a business card for my restaurant group I own. Four different concepts:

Copperfield Alehouse
Bristow Alehouse
Tanager's Stone Hearth Kitchen
Pellston Patty Company

Card doesn't need to include all the logos.

```html
<!DOCTYPE html>
<html lang="en">
<head>
<meta charset="utf-8">
<title>KRV Business Card</title>
<link rel="stylesheet" href="https://fonts.googleapis.com/css2?family=Poppins:wght@400;500;600&display=swap">
<style>
  :root {
    --backdrop: #262425;
    --gold: #d2ae6c;
    --white: #ffffff;
    --slate: #707073;
    --slate-pattern: #747478;
    --ink-light: #ffffff;
  }
  * { margin: 0; padding: 0; box-sizing: border-box; }
  html, body {
    width: 1125px; height: 1200px; overflow: hidden;
    background: var(--backdrop);
    font-family: "Poppins", sans-serif;
  }
  .card {
    position: absolute; left: 171px; width: 826px; height: 471px;
    overflow: hidden;
  }
  .card-front { top: 106px; background: var(--white); }
  .card-back { top: 639px; background: var(--slate); }

  .contact-panel {
    position: absolute; left: 0; top: 0; width: 378px; height: 100%;
    background: var(--gold); color: var(--ink-light);
    padding: 78px 0 0 37px;
  }
  .person-name { font-size: 31px; font-weight: 600; line-height: 1.15; }
  .person-title { font-size: 20px; font-weight: 400; line-height: 1.2; }
  .address { margin-top: 27px; font-size: 20px; line-height: 1.3; }
  .contact-lines { margin-top: 10px; font-size: 20px; line-height: 1.3; }

  .brand-block {
    position: absolute; left: 378px; right: 0; top: 124px;
    text-align: center; color: var(--gold);
  }
  .brand-initials { font-size: 84px; font-weight: 600; line-height: 1; letter-spacing: 4px; }
  .brand-name {
    margin-top: 14px; font-size: 30px; font-weight: 500;
    letter-spacing: 4px; line-height: 1.25; text-transform: uppercase;
  }

  .web-band {
    position: absolute; left: 378px; right: 0; top: 389px; height: 38px;
    background: var(--slate); color: var(--white);
    font-size: 20px; font-weight: 500; letter-spacing: 2px;
    display: flex; align-items: center; justify-content: center;
  }

  .back-pattern {
    position: absolute; inset: 0;
    background: linear-gradient(135deg, var(--slate-pattern), var(--slate));
  }
  .back-initials {
    position: absolute; left: 640px; top: 338px;
    font-size: 72px; font-weight: 600; color: var(--white);
    letter-spacing: 3px; line-height: 1;
  }
</style>
</head>
<body>
  <section class="card card-front">
    <div class="contact-panel">
      <p class="person-name">Daniel Harlow</p>
      <p class="person-title">President</p>
      <p class="address">4120 Alder Crest Road<br>Fairbanks, Alaska 99712</p>
      <p class="contact-lines">
        P. 555-214-7730<br>
        C. 555-618-2094<br>
        F. 555-309-4461<br>
        name@kestrelridge.com
      </p>
    </div>
    <div class="brand-block">
      <p class="brand-initials">KRV</p>
      <p class="brand-name">Kestrel Ridge<br>Ventures</p>
    </div>
    <div class="web-band">www.kestrelridge.com</div>
  </section>

  <section class="card card-back">
    <div class="back-pattern" role="img" aria-label="Faint repeating monogram pattern in slate grey"></div>
    <p class="back-initials">KRV</p>
  </section>
</body>
</html>
```